Copperleaf Roofing Business Card

This is my current business card. But I’d like to make some changes. Somewhere on the card I’d like to list some of the services we offer. Maybe on the back? But I’d still like to keep the red. White and black modern look.

-residential & commercial roofing
-Roof Repairs & Maintenance
-Storm Damage & Insurance Claims specialist
-Christmas Lights and permanent Christmas lights
Fencing. Windows. Gutters. Siding. Sheetrock, painting.

```html
<!DOCTYPE html>
<html lang="en">
<head>
<meta charset="utf-8">
<title>Copperleaf Roofing Business Card</title>
<link rel="stylesheet" href="https://fonts.googleapis.com/css2?family=Michroma&family=Roboto+Condensed:wght@400;500&display=swap">
<style>
  :root {
    --bg: #3a3a3a;
    --card-black: #050505;
    --red: #e0202a;
    --red-dark: #7a0e12;
    --white: #ffffff;
    --grey-text: #e8e8e8;
  }
  * { margin: 0; padding: 0; box-sizing: border-box; }
  html, body { width: 1200px; height: 694px; overflow: hidden; }
  body {
    background: var(--bg);
    font-family: "Roboto Condensed", Arial, sans-serif;
    position: relative;
  }
  .card {
    position: absolute;
    top: 187px;
    width: 560px;
    height: 320px;
    border-radius: 16px;
    overflow: hidden;
  }
  .card-front { left: 26px; }
  .card-back { left: 614px; background: var(--card-black); }

  .plaid-fill {
    position: absolute; inset: 0;
    background:
      linear-gradient(90deg, rgba(0,0,0,0) 0 38%, rgba(0,0,0,.55) 38% 58%, rgba(0,0,0,0) 58%),
      linear-gradient(180deg, rgba(255,255,255,0) 0 28%, rgba(255,255,255,.25) 28% 36%, rgba(255,255,255,0) 36% 62%, rgba(0,0,0,.45) 62% 78%, rgba(0,0,0,0) 78%),
      linear-gradient(135deg, var(--red) 0%, var(--red-dark) 55%, #b0151c 100%);
  }

  .front-logo {
    position: absolute; inset: 0;
    display: flex; flex-direction: column; align-items: center; justify-content: center;
    gap: 14px;
  }
  .logo-circle {
    width: 96px; height: 96px; border-radius: 50%;
    background: var(--red-dark);
    border: 4px solid var(--white);
    flex: none;
  }
  .logo-name {
    font-family: "Michroma", Arial, sans-serif;
    color: var(--white);
    text-align: center;
    line-height: 1.25;
    white-space: nowrap;
  }
  .front-logo .logo-name { font-size: 26px; }
  .front-logo .logo-name span { display: block; font-size: 17px; }

  .back-strip {
    position: absolute; right: 0; bottom: 0;
    width: 100%; height: 44px;
    background: linear-gradient(90deg, var(--card-black) 0%, var(--red-dark) 45%, var(--red) 100%);
    clip-path: polygon(30% 100%, 100% 0, 100% 100%);
  }
  .back-logo {
    position: absolute; left: 36px; top: 34px;
    display: flex; align-items: center; gap: 10px;
  }
  .back-logo .logo-circle { width: 52px; height: 52px; border-width: 3px; background: var(--red); }
  .back-logo .logo-name { color: var(--red); font-size: 13px; text-align: left; }
  .back-logo .logo-name span { display: block; font-size: 9px; color: var(--white); }

  .services {
    position: absolute; right: 20px; top: 34px; width: 262px;
    list-style: none;
    color: var(--grey-text);
    font-size: 12px; line-height: 1.6;
    white-space: nowrap;
  }
  .services li::before { content: "• "; color: var(--red); }
  .services .inline-items span::before { content: " • "; color: var(--red); }
  .services .inline-items span:first-child::before { content: ""; }

  .person { position: absolute; left: 36px; top: 168px; }
  .person-name {
    font-family: "Michroma", Arial, sans-serif;
    font-size: 18px; color: var(--white);
    white-space: nowrap;
  }
  .person-name .first { color: var(--red); }
  .person-title { color: var(--grey-text); font-size: 14px; margin-top: 4px; }

  .contact { list-style: none; margin-top: 12px; color: var(--white); font-size: 14px; }
  .contact li { display: flex; align-items: center; gap: 10px; line-height: 1.65; white-space: nowrap; }
  .contact svg { width: 14px; height: 14px; fill: var(--red); flex: none; }
</style>
</head>
<body>

<section class="card card-front">
  <div class="plaid-fill" role="img" aria-label="Red, black and white tartan pattern background"></div>
  <div class="front-logo">
    <div class="logo-circle"></div>
    <div class="logo-name">COPPERLEAF<span>ROOFING CO.</span></div>
  </div>
</section>

<section class="card card-back">
  <div class="back-strip" role="img" aria-label="Red tartan pattern band"></div>

  <div class="back-logo">
    <div class="logo-circle"></div>
    <div class="logo-name">COPPERLEAF<span>ROOFING CO.</span></div>
  </div>

  <ul class="services">
    <li>Residential &amp; commercial roofing</li>
    <li>Roof Repairs &amp; Maintenance</li>
    <li>Storm Damage &amp; Insurance Claims specialist</li>
    <li>Christmas Lights and permanent Christmas lights</li>
    <li class="inline-items"><span>Fencing</span><span>Windows</span><span>Gutters</span><span>Siding</span></li>
    <li class="inline-items"><span>Sheetrock</span><span>Painting</span></li>
  </ul>

  <div class="person">
    <div class="person-name"><span class="first">DALE</span> MERRITT</div>
    <div class="person-title">Owner</div>
    <ul class="contact">
      <li>
        <svg viewBox="0 0 24 24" aria-hidden="true"><path d="M6.6 10.8a15.1 15.1 0 0 0 6.6 6.6l2.2-2.2a1 1 0 0 1 1-.25 11.4 11.4 0 0 0 3.6.57 1 1 0 0 1 1 1V20a1 1 0 0 1-1 1A17 17 0 0 1 3 4a1 1 0 0 1 1-1h3.5a1 1 0 0 1 1 1c0 1.25.2 2.45.57 3.570a1 1 0 0 1-.25 1z"/></svg>
        682-555-0148
      </li>
      <li>
        <svg viewBox="0 0 24 24" aria-hidden="true"><path d="M2 5h20v14H2z M4 7v.5l8 5 8-5V7l-8 5z" fill-rule="evenodd"/></svg>
        dale@copperleafroofing.co
      </li>
      <li>
        <svg viewBox="0 0 24 24" aria-hidden="true"><path d="M12 2a10 10 0 1 0 0 20 10 10 0 0 0 0-20zm0 2c.9 1.2 1.6 2.6 2 4h-4c.4-1.4 1.1-2.8 2-4zM4.3 14a8 8 0 0 1 0-4h3.4a16 16 0 0 0 0 4zm.8 2h3c.3 1.3.8 2.5 1.4 3.6A8 8 0 0 1 5.1 16zm3-8h-3a8 8 0 0 1 4.4-3.6C7.9 5.5 7.4 6.7 8.1 8zM12 20c-.9-1.2-1.6-2.6-2-4h4c-.4 1.4-1.1 2.8-2 4zm2.3-6H9.7a14 14 0 0 1 0-4h4.6a14 14 0 0 1 0 4zm.2 5.6c.6-1.1 1.1-2.3 1.4-3.6h3a8 8 0 0 1-4.4 3.6zM16.3 14a16 16 0 0 0 0-4h3.4a8 8 0 0 1 0 4zm-.4-6c-.3-1.3-.8-2.5-1.4-3.6A8 8 0 0 1 18.9 8z"/></svg>
        www.copperleafroofing.co
      </li>
    </ul>
  </div>
</section>

</body>
</html>
```